Window and GutterCleaning Flyer A5 size double sided.

We need a double sided A5 flyer. Side 1, is for window cleaning, side 2 is for gutter cleaning. Licensed by Borough of Marlow Council.
Phone number 0800 473 1926.
Business address 17 Fallowmere Close, North Brack Edinburgh EH31 4LP.
www.clearpane-hub-services.com
We use a LoftEye Gutter inspection Cam to view your gutters first to see if they need doing.
Window cleaning ; Professional window cleaning services, what we offer, water fed pole window cleaning able to reach windows up to 60 feet.
Conservatory cleaning.
Conservatory roof cleaning.
Fascias & Soffits cleaning.
Excellent Customer Service.
Target Market(s)
domestic houses
Industry/Entity Type
window cleaning
Look and feel
Each slider illustrates characteristics of the customer's brand and the style your logo design should communicate.

```html
<!DOCTYPE html>
<html lang="en">
<head>
<meta charset="utf-8">
<title>ClearPane Hub – Window &amp; Gutter Cleaning Flyer</title>
<link rel="stylesheet" href="https://fonts.googleapis.com/css2?family=Poppins:wght@300;400;500;600;700;800;900&display=swap">
<style>
:root{
  --navy:#2d2a6b;
  --navy-dark:#26235e;
  --sky:#a9cdee;
  --sky-text:#8fbde8;
  --gold:#e2b43b;
  --sun:#fbd36a;
  --white:#ffffff;
  --ink:#1f1d45;
  --rule:#b9b9c9;
}
*{box-sizing:border-box;margin:0;padding:0}
html,body{width:1200px;height:3069px;overflow:hidden;background:var(--white)}
body{position:relative;font-family:"Poppins",sans-serif;color:var(--navy)}
.flyer{position:absolute;left:110px;width:988px;height:1404px;overflow:hidden;background:var(--white);box-shadow:0 6px 18px rgba(0,0,0,.35)}
.flyer--windows{top:90px;background:radial-gradient(circle at 520px 110px,#fff6d6 0,var(--sun) 90px,#fde7a6 260px,#fff5dc 480px,#ffffff 720px)}
.flyer--gutters{top:1600px}
.abs{position:absolute}
.brand{display:flex;align-items:center;gap:12px;font-weight:800;color:var(--navy);font-size:34px;line-height:1.05}
.brand__square{width:22px;height:22px;background:var(--sky);flex:none}
.hex-art{position:absolute;left:0;top:0}
.badge{position:absolute;border-radius:50%;background:radial-gradient(circle,#fff3c4 0 38%,var(--gold) 40% 100%);border:6px solid #c9971f;box-shadow:0 3px 8px rgba(0,0,0,.3)}
.center{text-align:center}
.kicker{font-weight:400;font-size:43px;line-height:1.03;color:var(--navy)}
.headline{font-weight:900;font-size:72px;line-height:.9;color:var(--navy);letter-spacing:-1px}
.spaced{font-weight:500;font-size:40px;letter-spacing:15px;color:var(--sky-text)}
.intro{font-size:18px;line-height:1.22;color:var(--ink)}
.section-title{font-weight:800;font-size:40px;color:var(--navy)}
.section-title span{color:var(--sky-text)}
.offer{position:absolute;display:flex;align-items:flex-start;gap:20px;font-size:21px;line-height:1.2;color:var(--navy)}
.icon{width:50px;height:50px;border-radius:50%;flex:none;display:flex;align-items:center;justify-content:center}
.icon--sky{background:var(--sky)}
.icon--navy{background:var(--navy)}
.icon svg{width:26px;height:26px}
.rule-h{position:absolute;height:0;border-top:1px dotted var(--rule)}
.rule-v{position:absolute;width:0;border-left:1px dotted var(--rule)}
.licensed{font-weight:800;font-size:31px;color:var(--sky-text)}
.council{font-weight:600;font-size:24px;color:var(--navy)}
.band{position:absolute;left:0;width:988px;background:var(--navy)}
.quote-box{position:absolute;background:var(--sky);border-radius:12px;display:flex;align-items:center;justify-content:center;text-align:center;font-weight:700;font-size:25px;line-height:1.3;color:var(--navy)}
.qmark{position:absolute;font-weight:900;font-size:74px;line-height:1;color:var(--navy)}
.cta{font-weight:800;font-size:31px;color:var(--sky)}
.contact{display:flex;align-items:center;gap:12px;color:var(--white);font-size:21px}
.contact--bold{font-weight:700;font-size:24px}
.contact svg{width:22px;height:22px;flex:none}
.base{font-weight:800;font-size:22px;line-height:1.1;color:var(--white)}
.base span{color:var(--sky)}
.addr{display:flex;gap:12px;align-items:flex-start;color:var(--white);font-size:19px;line-height:1.2}
.addr svg{width:28px;height:28px;flex:none;margin-top:6px}
.promo{position:absolute;background:var(--sky)}
.free{font-weight:900;font-size:66px;line-height:.9;color:var(--white)}
.promo-head{font-weight:800;font-size:25px;line-height:1;color:var(--navy);white-space:nowrap}
.promo-text{font-size:21px;line-height:1.15;color:var(--navy)}
.why{position:absolute;display:flex;align-items:center;gap:10px;font-weight:600;font-size:16px;line-height:1.15;color:var(--navy)}
.why .icon{width:48px;height:48px}
</style>
</head>
<body>

<section class="flyer flyer--windows">
  <svg class="hex-art" width="988" height="1000" viewBox="0 0 988 1000" role="img" aria-label="Photos of a cleaner using a water-fed pole on house windows, a squeegee on wet glass and a clean conservatory roof">
    <defs>
      <linearGradient id="brick" x1="0" y1="0" x2="1" y2="1"><stop offset="0" stop-color="#a4634a"/><stop offset="1" stop-color="#6e3a2b"/></linearGradient>
      <linearGradient id="house" x1="0" y1="0" x2="0" y2="1"><stop offset="0" stop-color="#8c6a5c"/><stop offset=".6" stop-color="#b7a79c"/><stop offset="1" stop-color="#6f6a60"/></linearGradient>
      <linearGradient id="water" x1="0" y1="0" x2="1" y2="1"><stop offset="0" stop-color="#3e6fae"/><stop offset="1" stop-color="#9cb8d8"/></linearGradient>
      <linearGradient id="conserv" x1="0" y1="0" x2="0" y2="1"><stop offset="0" stop-color="#b9d0ea"/><stop offset=".6" stop-color="#e8edf2"/><stop offset="1" stop-color="#8a5a44"/></linearGradient>
    </defs>
    <g stroke="#2d2a6b" stroke-width="12">
      <polygon points="0,-1 .866,-.5 .866,.5 0,1 -.866,.5 -.866,-.5" transform="translate(838 216) scale(186)" fill="url(#brick)" vector-effect="non-scaling-stroke"/>
      <polygon points="0,-1 .866,-.5 .866,.5 0,1 -.866,.5 -.866,-.5" transform="translate(946 486) scale(180)" fill="url(#water)" vector-effect="non-scaling-stroke"/>
      <polygon points="0,-1 .866,-.5 .866,.5 0,1 -.866,.5 -.866,-.5" transform="translate(676 474) scale(176)" fill="url(#house)" vector-effect="non-scaling-stroke"/>
      <polygon points="0,-1 .866,-.5 .866,.5 0,1 -.866,.5 -.866,-.5" transform="translate(838 800) scale(190)" fill="url(#conserv)" vector-effect="non-scaling-stroke"/>
    </g>
  </svg>
  <div class="badge" style="left:502px;top:630px;width:160px;height:160px"></div>

  <div class="abs brand" style="left:150px;top:140px"><span class="brand__square"></span>ClearPane<br>Hub</div>

  <div class="abs kicker center" style="left:58px;top:312px;width:420px">LET THE<br>SUNSHINE IN</div>
  <div class="abs headline" style="left:55px;top:412px">SPARKLING<br>WINDOWS</div>
  <div class="abs spaced" style="left:54px;top:538px">GUARANTEED</div>
  <p class="abs intro center" style="left:30px;top:598px;width:460px">We offer high-quality window cleaning for<br>homes and businesses, delivering. We only<br>clean domestic properties not businesses.<br>Spotless, streak-free results every time.<br>As per last info, can't claim this too.</p>

  <h2 class="abs section-title" style="left:68px;top:742px"><span>WE</span> OFFER</h2>

  <div class="offer" style="left:70px;top:808px">
    <span class="icon icon--sky"><svg viewBox="0 0 24 24" fill="none" stroke="#fff" stroke-width="2"><path d="M4 20L18 4M15 4h4v4"/></svg></span>
    <span>Water-Fed Pole<br>Cleaning – Up to<br>60 Feet</span>
  </div>
  <div class="offer" style="left:70px;top:910px">
    <span class="icon icon--navy"><svg viewBox="0 0 24 24" fill="none" stroke="#fff" stroke-width="2"><path d="M4 10l8-5 8 5v10H4zM9 20v-8M15 20v-8M4 14h16"/></svg></span>
    <span>Conservatory<br>Windows<br>&amp; Roofs</span>
  </div>
  <div class="offer" style="left:70px;top:1012px">
    <span class="icon icon--sky"><svg viewBox="0 0 24 24" fill="none" stroke="#fff" stroke-width="2"><path d="M3 9l9-5 9 5M5 9v11h14V9"/></svg></span>
    <span>Fascia &amp;<br>Soffit Cleaning</span>
  </div>
  <div class="offer" style="left:401px;top:808px">
    <span class="icon icon--navy"><svg viewBox="0 0 24 24" fill="none" stroke="#fff" stroke-width="2"><path d="M12 3v18M6 9h12M8 21h8"/></svg></span>
    <span>One-off or<br>Regular<br>Cleans</span>
  </div>
  <div class="offer" style="left:401px;top:910px">
    <span class="icon icon--sky"><svg viewBox="0 0 24 24" fill="none" stroke="#fff" stroke-width="2"><path d="M5 12l5 5 9-10"/></svg></span>
    <span>Reliable,<br>Friendly<br>Service</span>
  </div>

  <div class="rule-h" style="left:68px;top:892px;width:282px"></div>
  <div class="rule-h" style="left:68px;top:994px;width:282px"></div>
  <div class="rule-h" style="left:380px;top:892px;width:280px"></div>
  <div class="rule-h" style="left:380px;top:994px;width:280px"></div>
  <div class="rule-v" style="left:366px;top:812px;height:255px"></div>

  <div class="abs licensed" style="left:408px;top:1030px">LICENSED BY</div>
  <div class="abs council" style="left:652px;top:1036px">Borough of Marlow Council</div>

  <div class="band" style="top:1158px;height:246px"></div>
  <div class="quote-box" style="left:70px;top:1116px;width:848px;height:100px">Great service from start to finish. Reliable, professional<br>and the windows have never looked better!</div>
  <div class="qmark" style="left:100px;top:1080px">“</div>
  <div class="qmark" style="left:852px;top:1198px;color:var(--white)">”</div>

  <div class="abs cta" style="left:70px;top:1248px">GET FREE QUOTE NOW</div>
  <div class="abs contact contact--bold" style="left:70px;top:1300px">
    <svg viewBox="0 0 24 24"><circle cx="12" cy="12" r="12" fill="#a9cdee"/><path d="M8 6l2 3-1.5 1.5a8 8 0 004 4L14 13l3 2-1 2.5c-5 0-10-5-10-10z" fill="#2d2a6b"/></svg>0800 473 1926
  </div>
  <div class="abs contact" style="left:70px;top:1336px">
    <svg viewBox="0 0 24 24" fill="none" stroke="#a9cdee" stroke-width="1.6"><circle cx="12" cy="12" r="10"/><path d="M2 12h20M12 2c3 3 3 17 0 20M12 2c-3 3-3 17 0 20"/></svg>www.clearpane-hub-services.com
  </div>

  <div class="abs base" style="left:574px;top:1256px">BASED IN NORTH BRACK<br><span>SERVING ALL OF EDINBURGH</span></div>
  <div class="abs addr" style="left:568px;top:1316px">
    <svg viewBox="0 0 24 24"><path d="M12 2a7 7 0 017 7c0 5-7 13-7 13S5 14 5 9a7 7 0 017-7z" fill="#a9cdee"/><circle cx="12" cy="9" r="2.5" fill="#2d2a6b"/></svg>
    <span>17 Fallowmere Close, North Brack,<br>Edinburgh EH31 4LP</span>
  </div>
</section>

<section class="flyer flyer--gutters">
  <svg class="hex-art" width="600" height="1000" viewBox="0 0 600 1000" role="img" aria-label="Photos of a house roofline with gutter, fascia and soffit labelled, a vacuum hose clearing a gutter, and a gloved hand removing leaves">
    <defs>
      <linearGradient id="roof" x1="0" y1="0" x2="1" y2="1"><stop offset="0" stop-color="#d9dde0"/><stop offset=".5" stop-color="#f2f2f2"/><stop offset="1" stop-color="#8d6b5a"/></linearGradient>
      <linearGradient id="pipe" x1="0" y1="0" x2="1" y2="1"><stop offset="0" stop-color="#4e5d47"/><stop offset="1" stop-color="#857a63"/></linearGradient>
      <linearGradient id="vac" x1="0" y1="0" x2="1" y2="1"><stop offset="0" stop-color="#c7c2b8"/><stop offset=".6" stop-color="#ece9e2"/><stop offset="1" stop-color="#3a4aa3"/></linearGradient>
      <linearGradient id="leaves" x1="0" y1="0" x2="1" y2="1"><stop offset="0" stop-color="#9aa3a8"/><stop offset=".5" stop-color="#b0612c"/><stop offset="1" stop-color="#d7d3cc"/></linearGradient>
    </defs>
    <g stroke="#2d2a6b" stroke-width="12">
      <polygon points="0,-1 .866,-.5 .866,.5 0,1 -.866,.5 -.866,-.5" transform="translate(161 206) scale(180)" fill="url(#roof)" vector-effect="non-scaling-stroke"/>
      <polygon points="0,-1 .866,-.5 .866,.5 0,1 -.866,.5 -.866,-.5" transform="translate(70 514) scale(168)" fill="url(#pipe)" vector-effect="non-scaling-stroke"/>
      <polygon points="0,-1 .866,-.5 .866,.5 0,1 -.866,.5 -.866,-.5" transform="translate(322 508) scale(180)" fill="url(#vac)" vector-effect="non-scaling-stroke"/>
      <polygon points="0,-1 .866,-.5 .866,.5 0,1 -.866,.5 -.866,-.5" transform="translate(154 814) scale(180)" fill="url(#leaves)" vector-effect="non-scaling-stroke"/>
    </g>
  </svg>
  <div class="badge" style="left:348px;top:180px;width:160px;height:160px"></div>

  <div class="abs brand" style="left:650px;top:126px"><span class="brand__square"></span>ClearPane<br>Hub</div>

  <div class="abs center" style="left:470px;top:280px;width:508px">
    <div class="kicker" style="font-size:31px">DON’T LET BLOCKED</div>
    <div class="headline" style="font-size:55px;line-height:.93;margin-top:4px">GUTTERS CAUSE<br>COSTLY DAMAGE</div>
    <div class="promo-text" style="font-size:31px;line-height:1.15;margin-top:16px">We inspect before we clean<br>saving you time and money</div>
  </div>

  <div class="promo" style="left:319px;top:532px;width:669px;height:236px"></div>
  <div class="abs" role="img" aria-label="Handheld inspection camera monitor showing a house" style="left:496px;top:566px;width:162px;height:120px;border-radius:10px;background:linear-gradient(135deg,#3c3f45,#6a8fb4 45%,#2f3236)"></div>
  <div class="abs" style="left:672px;top:560px">
    <div class="free">FREE</div>
    <div class="promo-head" style="margin-top:6px">GUTTER CHECK<br>WITH LOFTEYE<br>INSPECTION CAM</div>
  </div>
  <div class="abs promo-text" style="left:496px;top:712px;width:470px">We show you what’s really going on before recommending service</div>

  <h2 class="abs section-title" style="left:470px;top:800px;width:388px;text-align:center"><span>WE</span> OFFER</h2>

  <div class="offer" style="left:356px;top:878px">
    <span class="icon icon--sky"><svg viewBox="0 0 24 24" fill="none" stroke="#fff" stroke-width="2"><circle cx="12" cy="12" r="9"/><path d="M6 6l12 12"/></svg></span>
    <span>Safe, No-Ladder<br>Cleaning</span>
  </div>
  <div class="offer" style="left:356px;top:956px">
    <span class="icon icon--navy"><svg viewBox="0 0 24 24" fill="none" stroke="#fff" stroke-width="2"><path d="M4 10l8-6 8 6v10H4zM9 14h6"/></svg></span>
    <span>Prevents Overflow,<br>Damp &amp; Water<br>Damage</span>
  </div>
  <div class="offer" style="left:690px;top:878px">
    <span class="icon icon--navy"><svg viewBox="0 0 24 24" fill="none" stroke="#fff" stroke-width="2"><path d="M5 19C5 10 11 5 19 5c0 8-5 14-14 14zM5 19l8-8"/></svg></span>
    <span>Removes Moss,<br>Leaves &amp; Debris</span>
  </div>
  <div class="offer" style="left:690px;top:956px">
    <span class="icon icon--sky"><svg viewBox="0 0 24 24" fill="none" stroke="#fff" stroke-width="2"><circle cx="12" cy="13" r="8"/><path d="M12 9v4l3 2M9 2h6"/></svg></span>
    <span>Fast, Clean &amp;<br>Fully Insured</span>
  </div>
  <div class="rule-h" style="left:354px;top:942px;width:280px"></div>
  <div class="rule-h" style="left:667px;top:942px;width:280px"></div>
  <div class="rule-v" style="left:651px;top:880px;height:170px"></div>

  <h2 class="abs section-title" style="left:200px;top:1054px;width:586px;text-align:center"><span>WHY</span> CHOOSE US?</h2>

  <div class="band" style="top:1164px;height:240px"></div>
  <div class="promo" style="left:70px;top:1115px;width:848px;height:100px;border-radius:12px"></div>
  <div class="why" style="left:94px;top:1130px">
    <span class="icon icon--navy"><svg viewBox="0 0 24 24" fill="none" stroke="#fff" stroke-width="2"><circle cx="12" cy="8" r="4"/><path d="M4 21c1-5 15-5 16 0"/></svg></span>
    <span>Friendly,<br>professional<br>service</span>
  </div>
  <div class="why" style="left:299px;top:1140px">
    <span class="icon icon--navy"><svg viewBox="0 0 24 24" fill="none" stroke="#fff" stroke-width="2"><path d="M5 12l5 5 9-10"/></svg></span>
    <span>Reliable and<br>efficient</span>
  </div>
  <div class="why" style="left:508px;top:1140px">
    <span class="icon icon--navy"><svg viewBox="0 0 24 24" fill="none" stroke="#fff" stroke-width="2"><rect x="5" y="3" width="14" height="18" rx="2"/><path d="M9 8h6M9 12h6"/></svg></span>
    <span>Fully licensed<br>and insured</span>
  </div>
  <div class="why" style="left:724px;top:1130px">
    <span class="icon icon--navy"><svg viewBox="0 0 24 24" fill="#fff"><path d="M12 3l2.6 5.5 6 .7-4.5 4.1 1.2 6L12 16.4 6.7 19.3l1.2-6L3.4 9.2l6-.7z"/></svg></span>
    <span>Excellent<br>customer<br>satisfaction</span>
  </div>

  <div class="abs cta" style="left:70px;top:1242px;color:var(--white)">STAY AHEAD OF LEAKS</div>
  <div class="abs" style="left:72px;top:1280px;font-weight:800;font-size:19px;color:var(--sky)">BOOK YOUR GUTTER CHECK TODAY!</div>
  <div class="abs contact contact--bold" style="left:70px;top:1316px">
    <svg viewBox="0 0 24 24"><circle cx="12" cy="12" r="12" fill="#a9cdee"/><path d="M8 6l2 3-1.5 1.5a8 8 0 004 4L14 13l3 2-1 2.5c-5 0-10-5-10-10z" fill="#2d2a6b"/></svg>0800 473 1926
  </div>
  <div class="abs contact" style="left:70px;top:1352px">
    <svg viewBox="0 0 24 24" fill="none" stroke="#a9cdee" stroke-width="1.6"><circle cx="12" cy="12" r="10"/><path d="M2 12h20M12 2c3 3 3 17 0 20M12 2c-3 3-3 17 0 20"/></svg>www.clearpane-hub-services.com
  </div>

  <div class="abs base" style="left:510px;top:1262px">BASED IN NORTH BRACK<br><span>SERVING ALL OF EDINBURGH</span></div>
  <div class="abs addr" style="left:504px;top:1320px">
    <svg viewBox="0 0 24 24"><path d="M12 2a7 7 0 017 7c0 5-7 13-7 13S5 14 5 9a7 7 0 017-7z" fill="#a9cdee"/><circle cx="12" cy="9" r="2.5" fill="#2d2a6b"/></svg>
    <span>Licensed by Borough of Marlow Council<br>Professional. Affordable. Local.</span>
  </div>
</section>

</body>
</html>
```